Melorix artwork for new single release

I need Melorix artwork creating to release a new single on there.

The specs are:

Ideal size: 3000 x 3000 pixels
Minimum size: 1400 x 1400 pixels
Aspect ratio: 1:1 (must be a perfect square)
File format: JPG or PNG
Color space: sRGB
File size: Max 4MB

The song is called "Was It Ever Rain?"
The artist is "Martin Hollow"

We have no images of Martin, so it really is open to imagination.

Target Market(s)

Melorix listeners

Industry/Entity Type

Music

```html
<!DOCTYPE html>
<html lang="en">
<head>
<meta charset="utf-8">
<title>Was It Ever Rain? — Martin Hollow</title>
<link rel="stylesheet" href="https://fonts.googleapis.com/css2?family=Pinyon+Script&family=Roboto+Condensed:wght@300&display=swap">
<style>
  :root {
    --night: #0a0612;
    --heart-light: #7a6c84;
    --heart-mid: #4a4259;
    --heart-dark: #221d2e;
    --ink-white: #ffffff;
  }
  * { margin: 0; padding: 0; box-sizing: border-box; }
  html, body {
    width: 1200px;
    height: 1200px;
    overflow: hidden;
    background: var(--night);
  }
  .cover {
    position: relative;
    width: 1200px;
    height: 1200px;
    background: var(--night);
    overflow: hidden;
  }
  .heart-art {
    position: absolute;
    left: 40px;
    top: 60px;
    width: 1120px;
    height: 1060px;
    background:
      radial-gradient(ellipse 55% 45% at 30% 30%, rgba(122, 108, 132, 0.85) 0%, rgba(122, 108, 132, 0) 70%),
      radial-gradient(ellipse 50% 55% at 50% 48%, var(--heart-mid) 0%, var(--heart-dark) 55%, rgba(10, 6, 18, 0) 80%);
  }
  .single-title {
    position: absolute;
    left: 0;
    right: 0;
    top: 238px;
    text-align: center;
    font-family: "Pinyon Script", cursive;
    font-weight: 400;
    font-size: 212px;
    line-height: 188px;
    color: var(--ink-white);
    text-shadow: 6px 10px 14px rgba(0, 0, 0, 0.55);
  }
  .single-title .line { display: block; }
  .artist-name {
    position: absolute;
    left: 0;
    right: 0;
    top: 1094px;
    text-align: center;
    font-family: "Roboto Condensed", sans-serif;
    font-weight: 300;
    font-size: 72px;
    line-height: 1;
    letter-spacing: 0.38em;
    padding-left: 0.38em;
    color: var(--ink-white);
    text-transform: uppercase;
  }
</style>
</head>
<body>
  <main class="cover">
    <div class="heart-art" role="img" aria-label="Shattered faceted heart in muted purple-grey shards"></div>

    <h1 class="single-title">
      <span class="line">Was It</span>
      <span class="line">Ever</span>
      <span class="line">Rain?</span>
    </h1>

    <p class="artist-name">Martin Hollow</p>
  </main>
</body>
</html>
```